Local Chiropractoc needs Modern Website

This website needs to have an upscale look with a very modern feel.

This is for a home page psd layout and an interior page psd file so 2 files total

Below is the information and websites to reference

Add Logo that is attached.

Build a color scheme similar to this website image titled "chiro-1" using the golds, whites, blacks and browns from the color of the logo

I want to see a light background so it makes the images and logo stick out

Must Include these pages in a horizontal menu bar in this order:
Home, Why Fair Ridge?, How Chiropractic Helps, Ask the Doctor, Work Place Wellness, Request an Appointment, Blog, Contact Us

Please add the following social media logos to the top and footer of the website: Chatterly, Plexo+, Vidzio

Build a "classy looking" Make An Appointment Button into the header with the contact info below

Phone Number:
555-014-2297

Address:
4172 North Maple Blvd, Suite #7
Cedar Point, FL 33990

This website needs 4 rotating banners. Please reference a layout similar to this for the banners: http://hollowpinespine.com/. However design it nicer than this website

Below are the description for each banner

Rotating Banner #1
Use Image: Patients are Saying
Add a line of text: "What our Patients are Saying"

Rotating Banner #2
Use Image: Becoming a Patient
Add a line of text: "Interested in Becoming a Patient"

Rotating Banner #3
Use Image: Dinner with Doctor
Add a line of text: "Win A free Dinner with Dr. Hollins"

Rotating Banner #4
Use Image: Chatterly
Add a line of text: Follow us on Chatterly
Bullet point these 4 lines underneath the "Follow us on Chatterly" text:
- Cutting Edge Health News
- Healthy Recipes
- Newest Health Products
- Clinic Events

I'd like to see a free consultation box similar to the "chiro-1" image. Fields to include are: First Name, Last Name, Phone Number, Comments

For the body, please fill it with latin text. Please design a professional 2 column layout similar to the www.hollowpinespine.com website. (DO NOT COPY THIS WEBSITE, USE IT AS REFERENCE)

In the left column include in this order:
Video
Rate us on Plexo Button, Find us on Chatterly Button
Welcome Letter

In the right column include this:

Office Hours
Monday: 8:00-11:00, 2:00-5:00
Tuesday: 8:30-11:00, 2:00-5:30
Wednesday: 8:00-11:00, 2:00-5:00
Thursday: 10:00-12:00, 2:30-5:00
Friday: 8:00-10:00, 1:00-5:00
Saturday: Closed
Sunday: Closed

Patient Testimonials
Fill with a latin text testimonial. This spot will rotate different testimonials

For the footer please design something similar to the layout of this: http://www.tidewellhealer.com/

Also include in the Footer: Powered by Crestline Pixel Group

```html
<!DOCTYPE html>
<html lang="en">
<head>
<meta charset="utf-8">
<title>Fair Ridge Chiropractic</title>
<link href="https://fonts.googleapis.com/css2?family=Ubuntu:ital,wght@0,400;0,500;0,700;1,400&display=swap" rel="stylesheet">
<style>
:root{
  --gold:#b8975a;
  --gold-dark:#a2834a;
  --gold-light:#c9ab72;
  --ink:#2a2a2a;
  --ink-soft:#3a3a3a;
  --cream:#f2eee7;
  --paper:#ffffff;
  --text:#555;
  --line:#e6e2da;
}
*{box-sizing:border-box;margin:0;padding:0}
html,body{width:912px;height:1200px;overflow:hidden}
body{background:var(--cream);font-family:"Ubuntu",sans-serif;color:var(--text);position:relative}
.abs{position:absolute}

/* header */
.brand{left:122px;top:50px;display:flex;align-items:center;gap:8px}
.brand-mark{width:18px;height:58px;background:var(--ink)}
.brand-name{font-size:30px;font-weight:700;color:var(--ink);line-height:1;letter-spacing:-.5px}
.brand-sub{font-size:14px;font-weight:700;color:var(--ink);letter-spacing:1.5px;margin-top:4px;line-height:1}
.top-social{left:740px;top:57px;display:flex;gap:4px}
.soc-dot{width:21px;height:21px;border-radius:50%;border:1.5px solid var(--gold);color:var(--gold);font-size:7px;font-weight:700;display:flex;align-items:center;justify-content:center}
.soc-dot.on{background:var(--gold);color:#fff}

.contact-bar{left:393px;top:88px;width:290px;height:35px;background:var(--ink);display:flex;align-items:center;color:#fff}
.cb-item{display:flex;align-items:center;gap:8px;padding:0 10px;height:100%}
.cb-item + .cb-item{border-left:1px solid #444}
.cb-main{font-size:8px;font-weight:700;line-height:1.2}
.cb-sub{font-size:7px;font-style:italic;color:#999}
.appt{left:673px;top:88px;width:133px;height:35px}
.appt span{position:absolute;left:24px;top:13px;font-size:7.5px;font-weight:700;color:var(--ink);letter-spacing:.2px}

/* nav */
.nav{left:105px;top:137px;width:701px;height:46px;background:var(--ink);display:flex;border-bottom:2px solid #222}
.nav a{color:#e8e8e8;text-decoration:none;font-size:7.5px;font-weight:500;display:flex;align-items:center;padding:0 12px;border-right:1px solid #3a3a3a;text-transform:uppercase}
.nav a:last-child{border-right:0}
.nav a.active{background:var(--gold);color:#fff}

/* hero */
.hero{left:105px;top:195px;width:701px;height:227px;overflow:hidden}
.hero-photo{position:absolute;inset:0;background:linear-gradient(110deg,#d9c2a4 0%,#e9d7c0 30%,#c98f6b 55%,#8a6a4e 80%)}
.consult{position:absolute;left:0;top:0;width:155px;height:227px;background:rgba(40,34,28,.72);padding:8px 11px;color:#fff}
.consult .pre{font-size:7px;text-align:center}
.consult .big{font-size:10.5px;font-weight:700;text-align:center;margin-top:2px}
.consult .tag{font-size:7.5px;font-style:italic;font-weight:500;text-align:center;margin-top:22px}
.field{position:absolute;left:11px;width:131px;height:19px;border:1px solid rgba(255,255,255,.8);background:rgba(255,255,255,.08);font-size:7px;font-style:italic;color:#fff;padding:5px 10px}
.field.lit{background:rgba(255,255,255,.75);color:#666}
.submit{position:absolute;left:11px;top:196px;width:59px;height:22px;background:var(--gold);color:#fff;font-size:7px;font-weight:700;padding:7px 11px}
.slide-text{position:absolute;left:512px;top:40px;width:170px;color:#fff}
.slide-text h2{font-size:16px;font-weight:500;line-height:1.3}
.slide-text p{font-size:7.5px;line-height:15px;margin-top:8px;text-align:justify}
.btn-light{display:inline-block;margin-top:10px;background:#fff;color:var(--ink);font-size:7px;padding:8px 11px;border-radius:2px}
.dots{position:absolute;left:513px;top:209px;display:flex;gap:3px}
.dots i{width:6px;height:6px;border-radius:50%;background:rgba(255,255,255,.45)}
.dots i.on{background:#fff}

/* main panel */
.panel{left:105px;top:433px;width:701px;height:653px;background:var(--paper);border:1px solid #e9e5dd}
.sec-title{position:absolute;display:flex;align-items:center;gap:6px;font-size:10px;font-weight:500;color:var(--ink);text-transform:uppercase}
.sec-title::before{content:"";width:3px;height:9px;background:var(--gold)}
.sec-title::after{content:"";flex:1;height:6px;background:#f4f2ee;margin-left:4px}
.video{left:17px;top:60px;width:439px;height:227px;border:1px solid var(--line);padding:6px}
.video-img{position:absolute;left:6px;top:6px;width:425px;height:191px;background:linear-gradient(180deg,#dcdcd8 0%,#b9bfa6 55%,#8e9a6a 100%)}
.play{position:absolute;left:198px;top:80px;width:30px;height:30px;background:rgba(255,255,255,.55);border:1px solid rgba(255,255,255,.8)}
.controls{position:absolute;left:6px;top:197px;width:425px;height:23px;background:#333;color:#aaa;font-size:6.5px;display:flex;align-items:center}
.controls .t{padding:0 8px}
.track{flex:1;height:3px;background:#555;position:relative}
.track b{position:absolute;left:0;top:0;width:30%;height:3px;background:var(--gold)}
.track b::after{content:"";position:absolute;right:-3px;top:-2px;width:6px;height:6px;border-radius:50%;background:#fff}
.ctl{width:22px;height:23px;border-left:1px solid #444;display:flex;align-items:center;justify-content:center}

.social-btn{position:absolute;top:341px;width:210px;height:45px;background:var(--ink);border-bottom:2px solid var(--gold);display:flex}
.social-btn .sq{width:45px;height:43px;background:var(--gold)}
.social-btn .lbl{padding:8px 0 0 40px;color:#fff}
.social-btn small{display:block;font-size:6.5px;font-weight:500}
.social-btn strong{display:block;font-size:19px;font-weight:500;color:var(--gold);letter-spacing:.5px;line-height:1.1}

.divider{position:absolute;left:0;top:422px;width:699px;height:1px;background:#f0ede7}
.letter{position:absolute;left:17px;top:477px;width:326px;font-size:7.6px;line-height:14.9px;text-align:justify}
.letter-img{position:absolute;left:359px;top:479px;width:325px;height:140px;background:linear-gradient(120deg,#a9c47a 0%,#d8b59a 40%,#e9d6c6 60%,#9db56d 100%)}

.hours{position:absolute;left:473px;top:35px;width:210px;border:1px solid var(--line)}
.hours h3{background:var(--gold);color:#fff;text-align:center;font-size:9.5px;font-weight:500;height:34px;line-height:34px}
.hours .row{display:flex;justify-content:space-between;height:23px;align-items:center;padding:0 11px;font-size:6.8px;border-top:1px solid #eee}
.hours .row:nth-child(even){background:#f4f4f4}
.hours .row b{color:var(--ink);font-weight:500}
.hours .row span{color:#888}
.hours .row.closed b,.hours .row.closed span{color:var(--gold)}
.testi{position:absolute;left:473px;top:283px;width:210px;height:83px;background:#f1f1f1;padding:14px 18px 0 20px;font-size:7px;font-style:italic;line-height:15px;color:#888}
.testi .q{position:absolute;left:18px;top:6px;font-size:40px;color:#d8d8d8;font-style:normal;font-weight:700;line-height:1}
.testi-bar{position:absolute;left:473px;top:366px;width:210px;height:22px;background:var(--gold);color:#fff;font-size:6.8px;font-weight:700;display:flex;align-items:center;justify-content:space-between;padding:0 10px 0 16px}
.testi-bar .dots{position:static;gap:2px}

/* footer */
.foot-links{left:0;top:1086px;width:912px;height:57px;background:var(--gold)}
.foot-links nav{position:absolute;left:122px;top:23px;font-size:7.6px;color:#fff;font-weight:500}
.foot-links nav a{color:#fff;text-decoration:none}
.foot-links nav .sep{margin:0 6px}
.foot-brand{position:absolute;left:722px;top:13px;display:flex;align-items:center;gap:4px;color:#fff}
.foot-brand .m{width:8px;height:28px;background:#fff}
.foot-brand b{font-size:13px;font-weight:700;display:block;line-height:1}
.foot-brand small{font-size:6.5px;font-weight:700;letter-spacing:.8px;display:block}
.foot-base{left:0;top:1143px;width:912px;height:57px;background:var(--ink);color:#fff;font-size:7.5px;font-weight:500}
.foot-addr{position:absolute;left:122px;top:20px;line-height:11px}
.foot-addr i{display:block;padding-left:28px;font-style:italic;font-weight:400}
.foot-soc{position:absolute;left:416px;top:17px;display:flex;gap:11px}
.foot-soc span{width:23px;height:23px;border:1px solid var(--gold);color:var(--gold);font-size:6.5px;font-weight:700;display:flex;align-items:center;justify-content:center;border-radius:2px}
.foot-soc span.on{background:var(--gold);color:#fff}
.foot-copy{position:absolute;left:637px;top:20px;line-height:11px;text-align:right;width:153px}
.foot-copy i{display:block;font-weight:400;font-style:italic}
.foot-copy i em{color:var(--gold)}
</style>
</head>
<body>

<header>
  <div class="abs brand">
    <div class="brand-mark"></div>
    <div>
      <div class="brand-name">FAIR RIDGE</div>
      <div class="brand-sub">CHIROPRACTIC</div>
    </div>
  </div>

  <div class="abs top-social">
    <span class="soc-dot">Ch</span>
    <span class="soc-dot on">P+</span>
    <span class="soc-dot">Vz</span>
  </div>

  <div class="abs contact-bar">
    <div class="cb-item">
      <svg width="16" height="16" viewBox="0 0 24 24"><path fill="#b8975a" d="M6.6 10.8a15 15 0 0 0 6.6 6.6l2.2-2.2c.3-.3.7-.4 1-.2 1.1.4 2.3.6 3.6.6.6 0 1 .4 1 1V20c0 .6-.4 1-1 1A17 17 0 0 1 3 4c0-.6.4-1 1-1h3.5c.6 0 1 .4 1 1 0 1.3.2 2.5.6 3.6.1.3 0 .7-.2 1z"/></svg>
      <div><div class="cb-main">555-014-2297</div><div class="cb-sub">info@example.com</div></div>
    </div>
    <div class="cb-item">
      <svg width="18" height="16" viewBox="0 0 24 20"><path fill="#b8975a" d="M12 1 1 10h3v9h6v-6h4v6h6v-9h3z"/></svg>
      <div><div class="cb-main">4172 North Maple Blvd, Suite #7</div><div class="cb-sub">Cedar Point, FL 33990</div></div>
    </div>
  </div>

  <div class="abs appt">
    <svg width="133" height="35" viewBox="0 0 133 35"><path d="M12 0H133V35H12L0 17.5Z" fill="#b8975a"/><path d="M17 3H130V32H17L7 17.5Z" fill="none" stroke="#d6bd8d" stroke-width="1"/></svg>
    <span>MAKE AN APPOINTMENT</span>
  </div>

  <nav class="abs nav">
    <a href="#">Home</a>
    <a href="#" class="active">Why Fair Ridge?</a>
    <a href="#">How Chiropractic Helps</a>
    <a href="#">Ask the Doctor</a>
    <a href="#">Work Place Wellness</a>
    <a href="#">Request an Appointment</a>
    <a href="#">Blog</a>
    <a href="#">Contact Us</a>
  </nav>
</header>

<section class="abs hero">
  <div class="hero-photo" role="img" aria-label="Photo of a smiling family of three close together"></div>
  <svg class="abs" style="left:0;top:0" width="701" height="227" viewBox="0 0 701 227">
    <path d="M460 0C470 40 500 70 490 115C480 160 470 190 476 227H701V0Z" fill="#b8975a" stroke="#fff" stroke-width="3"/>
  </svg>
  <form class="consult">
    <div class="pre">CONTACT US NOW &amp; GET YOUR</div>
    <div class="big">FREE CONSULTATION</div>
    <div class="tag">WELLNESS BEGINS HERE</div>
    <div class="field" style="top:73px">First Name</div>
    <div class="field lit" style="top:97px">Last Name</div>
    <div class="field" style="top:121px">Phone Number</div>
    <div class="field" style="top:145px;height:45px">Comments ...</div>
    <div class="submit">Submit ➜</div>
  </form>
  <div class="slide-text">
    <h2>What Our Patients<br>Are Saying?</h2>
    <p>Proin sit amet venenatis ante. Nulla lorem felis, maximus tincidunt felis nec, mattis con dimentum enim. Maecenas non sodales nund.</p>
    <span class="btn-light">Read More</span>
  </div>
  <div class="dots"><i></i><i class="on"></i><i></i><i></i></div>
</section>

<main class="abs panel">
  <h2 class="sec-title" style="left:17px;top:33px;width:439px">Our Videos</h2>
  <div class="abs video">
    <div class="video-img" role="img" aria-label="Video still of a three-generation family sitting outdoors"></div>
    <div class="play"><svg width="30" height="30" viewBox="0 0 30 30"><path d="M12 10l8 5-8 5z" fill="#555"/></svg></div>
    <div class="controls">
      <div class="ctl" style="border:0;border-right:1px solid #444"><svg width="8" height="8" viewBox="0 0 8 8"><path d="M1 0l7 4-7 4z" fill="#aaa"/></svg></div>
      <span class="t">00:28</span>
      <div class="track"><b></b></div>
      <span class="t">02:36</span>
      <div class="ctl"><svg width="9" height="8" viewBox="0 0 9 8"><path d="M0 2.5h2L5 0v8L2 5.5H0z" fill="#aaa"/></svg></div>
      <div class="ctl"><svg width="8" height="8" viewBox="0 0 8 8"><path d="M0 8L8 0M5 0h3v3M0 5v3h3" stroke="#aaa" fill="none"/></svg></div>
    </div>
  </div>

  <h2 class="sec-title" style="left:17px;top:314px;width:439px">We're on Social Medias</h2>
  <a class="social-btn" style="left:17px"><span class="sq"></span><span class="lbl"><small>RATE US ON</small><strong>PLEXO</strong></span></a>
  <a class="social-btn" style="left:245px"><span class="sq"></span><span class="lbl"><small>FIND US ON</small><strong>CHATTERLY</strong></span></a>

  <div class="divider"></div>

  <h2 class="sec-title" style="left:17px;top:453px;width:666px">Welcome Letter</h2>
  <div class="letter">
    Hello Dear Visitor,<br>
    Vestibulum malesuada tortor volutpat risus finibus, in consequat nibh dictum. Pellen tesque vestibulum nisi nisl, vel accumsan dui consequat sed. Integer non justo et mi interd um pretium. Proin ut pulvinar eros. Pellentesque at luctus odio, a ullamcorper urna. Nam semper feugiat massa non pulvinar. Curabitur sagittis, odio eget posuere ultricies, sem nisi pulvinar turpis, at laoreet arcu neque lacinia odio. Nulla nec nunc ac felis auctor fermentum quis ut justo. Donec ultricies feugiat accumsan. Integer leo justo, dapibus id mauris quis, vestibulum rutrum arcu. Etiam sed ipsum eu augue condimentum ullamcorper vel ac sapien. Cras sed lorem et est interdum commodo vitae sit amet orci. Ut mattis tempor metus sed venenatis.
  </div>
  <div class="letter-img" role="img" aria-label="Photo of a happy family of four outdoors in a park"></div>

  <div class="hours">
    <h3>OFFICE HOURS</h3>
    <div class="row"><b>Monday</b><span>8:00-11:00 AM, 2:00-5:00 PM</span></div>
    <div class="row"><b>Tuesday</b><span>8:30-11:00 AM, 2:00-5:30 PM</span></div>
    <div class="row"><b>Wednesday</b><span>8:00-11:00 AM, 2:00-5:00 PM</span></div>
    <div class="row"><b>Thursday</b><span>10:00-12:00 AM, 2:30-5:00 PM</span></div>
    <div class="row"><b>Friday</b><span>8:00-10:00 AM, 1:00-5:00 PM</span></div>
    <div class="row closed"><b>Saturday</b><span>Closed</span></div>
    <div class="row closed"><b>Sunday</b><span>Closed</span></div>
  </div>

  <h2 class="sec-title" style="left:473px;top:255px;width:210px">Patient Testimonials</h2>
  <blockquote class="testi">
    <span class="q">“</span>
    <span style="display:block;padding-left:30px">Pellentesque habitant morbi tristique senectus et netus et malesuada fames</span>
    ac turpis egestas. Donec faucibus aliquet dui, nec congue orci sagittis eget.
  </blockquote>
  <div class="testi-bar"><span>- Mr. Daniel Foster -</span><div class="dots"><i></i><i class="on"></i><i></i><i></i></div></div>
</main>

<footer>
  <div class="abs foot-links">
    <nav>
      <a href="#">Home</a><span class="sep">|</span><a href="#">Why Fair Ridge?</a><span class="sep">|</span><a href="#">How Chiropractic Helps</a><span class="sep">|</span><a href="#">Ask the Doctor</a><span class="sep">|</span><a href="#">Work Place Wellness</a><span class="sep">|</span><a href="#">Request an Appointment</a><span class="sep">|</span><a href="#">Blog</a><span class="sep">|</span><a href="#">Contact Us</a>
    </nav>
    <div class="foot-brand"><span class="m"></span><div><b>FAIR RIDGE</b><small>CHIROPRACTIC</small></div></div>
  </div>
  <div class="abs foot-base">
    <div class="foot-addr">4172 North Maple Blvd, Suite #7<i>Cedar Point, FL 33990</i></div>
    <div class="foot-soc"><span>Ch</span><span class="on">P+</span><span>Vz</span></div>
    <div class="foot-copy">Copyright © 2015, Fair Ridge Chiropractic<i>Powered by <em>Crestline Pixel Group</em></i></div>
  </div>
</footer>

</body>
</html>
```